Business Card for premium dental clinic

We are a premium dental clinic based in Brasov, Romania with more than 15 year on the market, providing quality dental treatment made by a team of more specialized dentists, working with modern equipment as a solution to beautiful and healthy teeth.

Our current logo for the clinic use 2 square with colors black and gold - dr Ternisu - studio, using family fonts Bodoni, Myriad Pro and Segoe Print.
Depending on the printing we used some gold CMYK background or gold foil picture background or a gold gradient.
We want a business card:
- eye catching business card
- distinguished business card
- premium design
- to keep the color scheme of black and gold
- to attract the customers to spent time reading the information
- modern concept

```html
<!DOCTYPE html>
<html lang="en">
<head>
<meta charset="utf-8">
<title>Lumeo Dental Clinic – Business Card</title>
<link rel="stylesheet" href="https://fonts.googleapis.com/css2?family=PT+Sans+Narrow:wght@400;700&display=swap">
<style>
  :root {
    --backdrop: #2a211d;
    --card: #2b2c2e;
    --gloss: #a3a5a9;
    --gloss-deep: #8d8f94;
    --gold: #c9a13a;
  }
  * { margin: 0; padding: 0; box-sizing: border-box; }
  html, body {
    width: 1200px;
    height: 800px;
    overflow: hidden;
    background: var(--backdrop);
  }
  .sheet {
    width: 1200px;
    height: 800px;
    display: flex;
    align-items: center;
    justify-content: center;
    gap: 40px;
  }
  .card {
    position: relative;
    width: 540px;
    height: 315px;
    background: var(--card);
    border: 2px solid var(--gold);
    border-radius: 3px;
    font-family: "PT Sans Narrow", "Arial Narrow", sans-serif;
    box-shadow: 0 14px 30px rgba(0, 0, 0, 0.45);
  }
  .brand {
    position: absolute;
    display: flex;
    align-items: center;
    gap: 14px;
    color: var(--gloss);
    font-weight: 400;
    line-height: 1;
    white-space: nowrap;
  }
  .brand-dot {
    flex: none;
    border-radius: 50%;
    background: var(--gloss);
  }
  .brand-name { letter-spacing: 0.02em; }

  .card-front .brand {
    left: 0; right: 0; top: 50%;
    transform: translateY(-50%);
    justify-content: center;
    font-size: 46px;
  }
  .card-front .brand-dot { width: 22px; height: 22px; }

  .card-back .doctor {
    position: absolute;
    left: 70px;
    top: 128px;
    color: var(--gloss-deep);
    font-size: 40px;
    font-weight: 400;
    line-height: 1;
    letter-spacing: 0.01em;
    white-space: nowrap;
    text-shadow: 0 1px 0 rgba(255, 255, 255, 0.08);
  }
  .card-back .doctor .title { font-size: 26px; margin-right: 4px; }
  .card-back .brand {
    right: 36px;
    top: 192px;
    font-size: 28px;
    gap: 10px;
  }
  .card-back .brand-dot { width: 14px; height: 14px; }
</style>
</head>
<body>
  <main class="sheet">
    <section class="card card-front" aria-label="Card front">
      <div class="brand">
        <span class="brand-dot"></span>
        <span class="brand-name">Lumeo Dental Clinic</span>
      </div>
    </section>

    <section class="card card-back" aria-label="Card back">
      <p class="doctor"><span class="title">dr.</span>Ternisu</p>
      <div class="brand">
        <span class="brand-dot"></span>
        <span class="brand-name">Lumeo Dental Clinic</span>
      </div>
    </section>
  </main>
</body>
</html>
```